Vanguard Honour Design Project

We have just won an award for customer service and would like to tell our users about how great we are!!

The award is the 3013 Coastal Vanguard Honour for excellence in Customer relations.

We have a in house made banner currently on our home page slider (www.velmorahome.com.au) but we would prefer something more professional.

Homepage Slides (image size: 636 x 313)

```html
<!DOCTYPE html>
<html lang="en">
<head>
<meta charset="utf-8">
<title>Velmora Home</title>
<link href="https://fonts.googleapis.com/css2?family=Arimo:wght@400;700&display=swap" rel="stylesheet">
<style>
:root{
  --wood:#8a5530;--wood-dark:#6b3d1f;--ink:#1c1c1c;--orange:#f0541c;--orange-lt:#f7731f;
  --nav:#6a5b52;--nav-active:#7a1a12;--lime:#8ea70a;--panel:#f1eeee;--text:#555;--head:#444;
  --link:#f05a1a;--red:#e0240e;--white:#fff;
}
*{box-sizing:border-box;margin:0;padding:0}
html,body{width:1200px;height:1000px;overflow:hidden}
body{font-family:"Arimo",Arial,sans-serif;background:linear-gradient(90deg,var(--wood-dark),var(--wood) 20%,#9a6238 50%,var(--wood) 80%,var(--wood-dark));position:relative}
.site{position:absolute;left:48px;top:16px;width:1111px;height:966px;background:var(--white);box-shadow:0 0 8px rgba(0,0,0,.5)}
.promo-bar{height:48px;background:var(--ink);color:var(--white);display:flex;align-items:center;justify-content:center;gap:10px;font-size:14px}
.promo-bar .btn{border:1px solid #888;border-radius:3px;padding:3px 7px;font-size:11px;background:#2c2c2c}
.masthead{position:absolute;top:50px;left:0;right:0;height:352px;background:linear-gradient(180deg,#f0561c,var(--orange-lt) 60%,#f36a1e)}
.brand{position:absolute;left:67px;top:28px;color:var(--white)}
.brand-name{font-size:30px;font-weight:700;letter-spacing:-.5px;display:flex;align-items:center;gap:8px}
.brand-name i{display:inline-block;width:18px;height:18px;border-radius:50%;background:var(--white)}
.brand-call{font-size:17px;margin-top:4px;color:#fde3d3}
.brand-call b{color:var(--white);font-size:17px}
.nav{position:absolute;left:67px;top:129px;width:960px;height:38px;background:var(--nav);display:flex;align-items:center;font-size:13px;font-weight:700;color:var(--white);z-index:2}
.nav a{padding:0 10px;height:100%;display:flex;align-items:center;white-space:nowrap}
.nav a.active{background:var(--nav-active)}
.nav .compare{margin-left:auto;margin-right:6px;background:var(--lime);height:28px;padding:0 9px}
.hero{position:absolute;left:67px;top:228px;width:637px;height:313px;background:linear-gradient(135deg,#d8ef3a,#b6dc22);overflow:hidden}
.hero .winner{position:absolute;left:58px;top:8px;font-size:32px;font-weight:700;color:#e01a12}
.hero .medal{position:absolute;left:300px;top:12px;width:268px;height:300px;border-radius:50% 50% 45% 45%;background:radial-gradient(circle,#fff6d8 40%,#f3c65a 60%,#d8962a)}
.hero .caption{position:absolute;left:0;top:90px;width:308px;height:134px;background:#fff9ee;padding:18px 20px}
.caption h2{font-size:22px;color:var(--link);line-height:1.2;font-weight:700;width:250px}
.caption a{display:block;margin-top:10px;font-size:14px;font-weight:700;color:#555}
.dots{position:absolute;left:24px;top:260px;display:flex;gap:12px}
.dots span{width:25px;height:25px;border-radius:50%;background:#3a3a3a;border:2px solid var(--white);color:var(--white);font-size:11px;font-weight:700;display:flex;align-items:center;justify-content:center}
.dots span.on{background:var(--orange)}
.panel{position:absolute;background:var(--panel);box-shadow:0 1px 3px rgba(0,0,0,.25)}
.shop{left:716px;top:228px;width:311px;height:313px;padding:14px 19px}
.shop-head{display:flex;justify-content:space-between;align-items:baseline;border-bottom:1px solid #ccc;padding-bottom:10px}
.shop-head h3{font-size:18px;color:#555}
.shop-head a,.shop .sub{font-size:12px;color:#777;text-decoration:underline}
.shop .cat{display:block;margin-top:11px;font-size:14px;font-weight:700;color:var(--link)}
.shop .cat.sale{margin-top:12px;color:var(--red)}
.shop .sub{display:block;margin-top:3px;line-height:1.4}
.card{top:562px;height:250px;padding:16px 21px}
.card h3{font-size:17px;color:var(--head);font-weight:700}
.card .tile{margin-top:20px;width:270px;height:86px}
.card p{font-size:12px;color:var(--text);line-height:1.35;margin-top:18px}
.card .go{position:absolute;left:21px;top:201px;height:29px;border-radius:15px;padding:0 14px;display:flex;align-items:center;color:var(--white);font-size:12px;font-weight:700;background:linear-gradient(#f58a3a,#e35d14)}
.card .go.red{background:linear-gradient(#f03a1a,#d21a08)}
.search-tile{background:linear-gradient(90deg,#e8ecf6,#f6f2ee)}
.specials-tile{background:#d90c0c;color:var(--white);font-size:46px;display:flex;align-items:center;justify-content:center}
.map-tile{background:var(--white);position:relative;padding:8px 4px;font-size:25px;font-weight:700;color:#111;line-height:1.2}
.map-tile small{position:absolute;right:4px;bottom:2px;font-size:12px}
.map-tile svg{position:absolute;right:18px;top:18px}
.card .note{color:var(--link);font-size:16px;margin-top:10px}
.card .hours{font-size:12px;color:#555;margin-top:8px}
.testimonial{position:absolute;top:834px;left:0;right:0;height:62px;background:linear-gradient(#eceaea,#f6f5f5);padding:12px 120px 12px 67px;font-size:14px;color:#666;line-height:1.45}
.footer-band{position:absolute;top:896px;left:0;right:0;height:70px;background:var(--orange);color:var(--white);font-size:18px;font-weight:700;display:flex;align-items:center;justify-content:center}
</style>
</head>
<body>
<div class="site">
  <div class="promo-bar">Save Time, Save Money, Book Your Onsite Measure Today! <span class="btn">BOOK NOW</span></div>
  <header class="masthead">
    <div class="brand">
      <div class="brand-name"><i></i>Velmora Home</div>
      <div class="brand-call">Call Now <b>1300 555 014</b></div>
    </div>
    <nav class="nav">
      <a class="active">Home</a><a>Search Our Carpets</a><a>Brands</a><a>About Us</a><a>Carpet Buyer Guide</a><a>Carpet Care</a><a>FAQS</a><a>Service Areas</a><a>Contact Us</a><a class="compare">Compare List</a>
    </nav>
  </header>

  <section class="hero">
    <div class="winner">WINNER</div>
    <div class="medal" role="img" aria-label="Gold laurel award medal for the 2013 Coastal Vanguard Honour, highly recommended for excellence in customer service"></div>
    <div class="caption">
      <h2>Customer service counts &amp; it's GREAT to be recognised!</h2>
      <a>Learn more »</a>
    </div>
    <div class="dots"><span>1</span><span class="on">2</span><span>3</span><span>4</span></div>
  </section>

  <aside class="panel shop">
    <div class="shop-head"><h3>Shop Now</h3><a>View Buyers Guide</a></div>
    <a class="cat sale">HALDANE SALE NOW ON! »</a>
    <a class="cat">Commercial Carpets »</a>
    <span class="sub">Marlowe Tessa, Marlowe Tessa Lights, Corrigan Stratus II, more »</span>
    <a class="cat">Domestic Carpets »</a>
    <span class="sub">Solana / Solbrook, Amara SDN by Loomcraft, Fenwick Kingsbury, more »</span>
    <a class="cat">Melb Specials &amp; Rentals »</a>
    <span class="sub">Carnival Bay, Corella by Ashleaf, Navaro SDN, more »</span>
    <a class="cat">View All Carpets »</a>
  </aside>

  <div class="panel card" style="left:67px;width:311px">
    <h3>SEARCH OUR FULL RANGE!</h3>
    <div class="tile search-tile" role="img" aria-label="Colourful search lettering with a magnifying glass"></div>
    <p>Marlowe, Fenwick, Ashleaf, Brindell, Haldane, Corrigan, Loomcraft, Questa &amp; many more! &gt;&gt;&gt;</p>
    <a class="go red">Start Search »</a>
  </div>
  <div class="panel card" style="left:392px;width:310px">
    <h3>Carpet Stock Specials</h3>
    <div class="tile specials-tile">Specials</div>
    <p>View our range of heavily discounted stock!</p>
    <a class="go">View Specials »</a>
  </div>
  <div class="panel card" style="left:716px;width:311px">
    <h3>Visit Our Showroom</h3>
    <div class="tile map-tile">212 Larchmont Rd<br>Kewdale
      <svg width="22" height="34" viewBox="0 0 22 34"><path d="M11 0C5 0 0 5 0 11c0 8 11 23 11 23s11-15 11-23C22 5 17 0 11 0z" fill="#e0140e"/><circle cx="11" cy="11" r="4" fill="#7a0a06"/></svg>
      <small>Mon-Sat</small></div>
    <div class="note">Samples available, Bring your Plans!</div>
    <div class="hours">Mon-Fri 9am - 5pm / Sat 10am - 4.30pm</div>
    <a class="go">View Location Maps »</a>
  </div>

  <div class="testimonial">We had two quotes for the same carpet and yours was hundreds of dollars cheaper, the quote was delivered faster and there was good follow-up compared to no follow-up. Your service was excellent and measures and layers came exactly when they said they would. Dan K. 3129 VIC</div>
  <div class="footer-band">Now installing carpet in Melbourne, Sydney, Geelong &amp; Mornington Peninsula.</div>
</div>
</body>
</html>
```